Public Speaking Book for aspiring, ambitious speakers

I'm looking for a 6x9 book cover (Brivora standard) as well as ebook and audiobook formats.

I'm looking for orange font on a white background as these are my brand colours.

Feel free to use some yellow and gold too if you deem it appropriate.

Title: Climb and Kindle
Subtitle: Find Your Voice. Tell Your Story. Share your Message.
Author: Owen Thistlewood

I would like to have a picture of a female speaker on the front cover.

Alternatively, some kind of image that symbolises public speaking like a microphone, podium etc

Target Market(s)

Aspiring professional speakers

Colors
f78f20

Requirements
Must have
• Correct spelling!
Nice to have
• A logo or picture that fits the theme, but no pressure if you can't think of anything
Should not have
• No men in suits please. I don't want this to have a 1980s corporate look.

```html
<!DOCTYPE html>
<html lang="en">
<head>
<meta charset="utf-8">
<title>Climb and Kindle — Owen Thistlewood</title>
<link rel="stylesheet" href="https://fonts.googleapis.com/css2?family=Montserrat:wght@400;500;600&display=swap">
<style>
  :root {
    --brand-orange: #f78f20;
    --band-black: #000000;
    --ink: #111111;
    --tagline-white: #ffffff;
    --photo-deep: #3e2208;
    --photo-brown: #6e3f10;
    --photo-amber: #9a6420;
    --photo-skin: #e3b896;
    --photo-skin-light: #f0d2bb;
    --photo-shirt: #f4eee9;
  }
  html, body {
    margin: 0;
    padding: 0;
    width: 803px;
    height: 1200px;
    overflow: hidden;
    background: #ffffff;
  }
  .cover {
    position: relative;
    width: 803px;
    height: 1200px;
    overflow: hidden;
    background: var(--brand-orange);
    font-family: "Montserrat", Arial, sans-serif;
  }
  .cover-photo {
    position: absolute;
    left: 0;
    top: 0;
    width: 803px;
    height: 566px;
    background:
      radial-gradient(ellipse 170px 110px at 740px 530px, var(--photo-shirt) 0%, rgba(244,238,233,0.85) 45%, rgba(244,238,233,0) 100%),
      radial-gradient(ellipse 150px 200px at 580px 380px, var(--photo-skin-light) 0%, rgba(240,210,187,0.7) 45%, rgba(240,210,187,0) 100%),
      radial-gradient(ellipse 230px 330px at 690px 170px, var(--photo-skin) 0%, rgba(227,184,150,0.85) 50%, rgba(227,184,150,0) 100%),
      linear-gradient(100deg, var(--photo-deep) 0%, var(--photo-brown) 30%, var(--photo-amber) 55%, var(--photo-brown) 100%);
  }
  .tagline {
    position: absolute;
    left: 51px;
    top: 104px;
    margin: 0;
    color: var(--tagline-white);
    font-weight: 500;
    font-size: 37px;
    line-height: 52px;
    letter-spacing: 2px;
  }
  .tagline span { display: block; }
  .title-band {
    position: absolute;
    left: 0;
    top: 566px;
    width: 803px;
    height: 289px;
    background: var(--band-black);
    display: flex;
    align-items: center;
    justify-content: center;
  }
  .title {
    margin: 0;
    color: var(--brand-orange);
    font-weight: 500;
    font-size: 126px;
    line-height: 132px;
    letter-spacing: -3px;
    text-align: center;
    text-transform: uppercase;
    white-space: nowrap;
  }
  .title span { display: block; }
  .author {
    position: absolute;
    left: 0;
    width: 803px;
    top: 1088px;
    margin: 0;
    text-align: center;
    color: var(--ink);
    font-weight: 600;
    font-size: 47px;
    letter-spacing: 0.5px;
  }
</style>
</head>
<body>
  <main class="cover">
    <div class="cover-photo" role="img" aria-label="Photograph of a female speaker in a white blouse holding a microphone, warm brown background"></div>
    <p class="tagline">
      <span>Find Your Voice.</span>
      <span>Tell Your Story.</span>
      <span>Share your Message.</span>
    </p>
    <div class="title-band">
      <h1 class="title"><span>Climb and</span><span>Kindle</span></h1>
    </div>
    <p class="author">Owen Thistlewood</p>
  </main>
</body>
</html>
```